Birchline Septic Solutions

Would like to see some single sided ones but would also like to see some double sided with one sided only being the logo. Owners name is Colin Vandro. Phone number is 555-214-0387
Services are pumping, inspections, installs, and repairs

Contact Information for Business Card

555-241-0387 Colin Vandro Maple Hollow, OH

```html
<!DOCTYPE html>
<html lang="en">
<head>
<meta charset="utf-8">
<title>Birchline Septic Solutions – Business Cards</title>
<link rel="stylesheet" href="https://fonts.googleapis.com/css2?family=Montserrat:wght@500;600;700;800&display=swap">
<style>
  :root {
    --stage: #1c1c1c;
    --ink: #0b0b0b;
    --paper: #ffffff;
    --teal: #2bbdb5;
    --mist: #dcdcdc;
    --shade: #2a2a2a;
    --card-w: 760px;
    --card-h: 434px;
  }
  * { box-sizing: border-box; margin: 0; padding: 0; }
  html, body {
    width: 1200px; height: 1015px; overflow: hidden;
    background: var(--stage);
    font-family: "Montserrat", Arial, sans-serif;
  }
  .canvas {
    position: relative; width: 1200px; height: 1015px;
    display: flex; flex-direction: column; align-items: center; justify-content: center; gap: 44px;
  }
  .card {
    position: relative; width: var(--card-w); height: var(--card-h);
    overflow: hidden; box-shadow: 0 14px 34px rgba(0,0,0,.55);
  }
  .card-bg { position: absolute; inset: 0; width: 100%; height: 100%; }

  /* Shared wordmark */
  .wordmark { position: absolute; display: flex; flex-direction: column; }
  .wordmark-row { display: flex; align-items: center; gap: 14px; }
  .wordmark-name {
    font-weight: 800; font-size: 82px; line-height: 1; letter-spacing: -1px;
    text-transform: uppercase;
  }
  .wordmark-dot { width: 22px; height: 22px; background: var(--teal); }
  .wordmark-tag {
    font-weight: 600; font-size: 22px; letter-spacing: 9px;
    text-transform: uppercase; margin-top: 12px; margin-left: 4px;
  }

  /* Front */
  .card-front { background: var(--ink); }
  .card-front .wordmark { left: 0; right: 0; top: 150px; align-items: center; }
  .card-front .wordmark-name { color: var(--paper); font-size: 86px; }
  .card-front .wordmark-tag { color: var(--mist); }

  /* Back */
  .card-back { background: var(--paper); }
  .card-back .wordmark { left: 150px; top: 292px; }
  .card-back .wordmark-name { color: var(--ink); font-size: 72px; }
  .card-back .wordmark-tag { color: var(--shade); font-size: 19px; letter-spacing: 8px; margin-top: 10px; }

  .contact { position: absolute; right: 48px; top: 40px; text-align: right; }
  .contact-name {
    color: var(--teal); font-weight: 800; font-size: 30px;
    text-transform: uppercase; letter-spacing: .5px; margin-bottom: 14px;
  }
  .contact-line {
    display: flex; align-items: center; justify-content: flex-end; gap: 10px;
    color: var(--paper); font-weight: 600; font-size: 19px; margin-top: 6px;
  }
  .contact-icon { width: 24px; height: 24px; flex: none; }

  .services {
    position: absolute; right: 48px; top: 196px; list-style: none; text-align: right;
  }
  .services li {
    color: var(--ink); font-weight: 600; font-size: 19px; text-transform: uppercase;
    line-height: 30px; display: flex; align-items: center; justify-content: flex-end; gap: 10px;
  }
  .services li::after {
    content: ""; width: 8px; height: 8px; border-radius: 50%; background: var(--teal);
  }
</style>
</head>
<body>
<main class="canvas">

  <section class="card card-front" aria-label="Business card front">
    <svg class="card-bg" viewBox="0 0 760 434" role="img" aria-label="Dark silhouette illustration of mountain peaks and pine forest">
      <defs>
        <linearGradient id="frontScene" x1="0" y1="0" x2="1" y2="1">
          <stop offset="0" stop-color="#050505"/>
          <stop offset="1" stop-color="#161616"/>
        </linearGradient>
      </defs>
      <rect width="760" height="434" fill="url(#frontScene)"/>
    </svg>
    <div class="wordmark">
      <div class="wordmark-row">
        <span class="wordmark-name">Birchline</span>
        <span class="wordmark-dot"></span>
      </div>
      <span class="wordmark-tag">Septic Solutions</span>
    </div>
  </section>

  <section class="card card-back" aria-label="Business card back">
    <svg class="card-bg" viewBox="0 0 760 434" role="img" aria-label="Illustration of snowy mountain and pine tree silhouettes fading into white">
      <defs>
        <linearGradient id="backScene" x1="0" y1="0" x2="0.3" y2="1">
          <stop offset="0" stop-color="#050505"/>
          <stop offset="0.6" stop-color="#1a1a1a"/>
          <stop offset="1" stop-color="#bdbdbd"/>
        </linearGradient>
      </defs>
      <polygon points="0,0 760,0 760,150 430,178 300,300 0,330" fill="url(#backScene)"/>
    </svg>

    <div class="contact">
      <p class="contact-name">Colin Vandro</p>
      <p class="contact-line">555-214-0387
        <svg class="contact-icon" viewBox="0 0 24 24" aria-hidden="true">
          <circle cx="12" cy="12" r="12" fill="var(--teal)"/>
          <path d="M8.2 6.5l2 2.2-1.2 1.5c.8 1.7 2 2.9 3.7 3.7l1.5-1.2 2.2 2-1.3 1.9c-4.2-.5-7.8-4.1-8.3-8.3z" fill="#0b0b0b"/>
        </svg>
      </p>
      <p class="contact-line">Maple Hollow, OH
        <svg class="contact-icon" viewBox="0 0 24 24" aria-hidden="true">
          <circle cx="12" cy="12" r="12" fill="var(--teal)"/>
          <path d="M12 5a4.5 4.5 0 0 0-4.5 4.5c0 3.3 4.5 8.5 4.5 8.5s4.5-5.2 4.5-8.5A4.5 4.5 0 0 0 12 5zm0 6.2a1.7 1.7 0 1 1 0-3.4 1.7 1.7 0 0 1 0 3.4z" fill="#0b0b0b"/>
        </svg>
      </p>
    </div>

    <ul class="services">
      <li>Pumping</li>
      <li>Inspections</li>
      <li>Installs</li>
      <li>Repairs</li>
    </ul>

    <div class="wordmark">
      <div class="wordmark-row">
        <span class="wordmark-name">Birchline</span>
        <span class="wordmark-dot"></span>
      </div>
      <span class="wordmark-tag">Septic Solutions</span>
    </div>
  </section>

</main>
</body>
</html>
```